Jewelers Website

This is for the DESIGN ONLY.
I am a software programmer and will be doing the development.
New website design for
www.lunacrestgems.com.au
Need a fresh new look for an online only jewellery business who produce their jewellery by hand. I would like it designed in a parallax style. Feel free to recommend fonts to use for the site. This is an Australian based company located in NSW so shots of sites in NSW might make nice background images.
http://vornaplex.me/demo/#theme=parallax
To contain the below sections
About Us
Contact Us
Gallery
Testimonials
Diamond Types
The colour scheme is to be Black / White and Silver.
With the Parallax style there will be moving sections and images for added impact.
Target Market(s)
Young Adults mainly engagement jewellery

```html
<!DOCTYPE html>
<html lang="en">
<head>
<meta charset="utf-8">
<title>Lunacrest Gems</title>
<link rel="stylesheet" href="https://fonts.googleapis.com/css2?family=Montserrat:wght@300;400;500&family=Open+Sans:ital,wght@0,400;0,600;1,400&display=swap">
<style>
:root{
  --black:#000;
  --ink:#2b2b2b;
  --muted:#6d6d6d;
  --white:#fff;
  --silver:#c9ccd0;
  --line:#e2e2e2;
  --footer:#222;
  --field:#3a3a3a;
  --card:rgba(30,30,30,.85);
  --sea1:#0d5f86;
  --sea2:#1fa0c9;
}
*{margin:0;padding:0;box-sizing:border-box}
html,body{width:1200px;height:3297px;overflow:hidden}
body{font-family:"Open Sans",Arial,sans-serif;color:var(--ink);background:var(--white);position:relative}
section,header,footer{position:absolute;left:0;width:1200px}
.center{text-align:center}
h2{font-family:"Montserrat",Arial,sans-serif;font-weight:300;font-size:38px;letter-spacing:1px}

/* header */
.hero{top:0;height:646px;background:radial-gradient(ellipse at 55% 40%,#4fb4dc 0%,#1b7aa6 40%,#0a3c58 100%)}
.hero-photo{position:absolute;inset:0}
.topbar{position:absolute;top:0;left:0;width:1200px;height:97px;background:rgba(20,20,20,.8)}
.brand{position:absolute;left:187px;top:28px;color:var(--white);font-family:"Montserrat",Arial,sans-serif;font-weight:400;font-size:20px;line-height:22px;letter-spacing:1px}
.nav{position:absolute;left:424px;top:43px;display:flex;gap:30px;list-style:none}
.nav li{font-family:"Montserrat",Arial,sans-serif;font-size:14px;color:#d8d8d8;letter-spacing:.3px}
.nav li.active{color:var(--white)}
.hero-band{position:absolute;left:193px;top:286px;width:811px;height:132px;background:rgba(20,40,60,.45)}
.hero-title{position:absolute;left:0;width:1200px;top:306px;color:var(--white);font-size:42px;font-weight:600;text-align:center}
.hero-sub{position:absolute;left:0;width:1200px;top:360px;color:var(--white);font-size:26px;font-weight:600;text-align:center}
.dots{position:absolute;left:568px;top:622px;display:flex;gap:6px}
.dots span{width:12px;height:12px;border-radius:50%;background:var(--white)}

/* about */
.about{top:646px;height:541px}
.about h2{position:absolute;top:56px;width:100%}
.lead{font-size:15px;color:#444;line-height:19px}
.about .lead{position:absolute;top:114px;left:220px;width:760px}
.small{font-size:11px;color:var(--muted);line-height:16px}
.about .small{position:absolute;top:166px;left:130px;width:940px}
.feature{position:absolute;top:288px;width:266px;height:207px;border:1px solid var(--line);text-align:center}
.feature svg{margin-top:26px}
.feature h3{font-family:"Montserrat",Arial,sans-serif;font-weight:400;font-size:19px;color:#444;margin-top:12px}
.feature p{font-size:10px;color:#888;line-height:15px;margin:10px 22px 0}

/* gallery */
.gallery{top:1187px;height:505px;background:linear-gradient(180deg,#8fd0ee 0%,#3fb3dc 25%,#1a93c2 55%,#2d7d5a 85%,#4a8a3b 100%)}
.gallery h2{position:absolute;top:44px;width:100%;color:#333}
.gallery .lead{position:absolute;top:92px;width:100%;font-size:14px;color:#222}
.thumb{position:absolute;width:196px;height:134px;border:5px solid var(--white)}
.t-silver{background:linear-gradient(135deg,#f2f2f2,#9a9a9a)}
.t-dark{background:radial-gradient(circle at 50% 50%,#bdbdbd 0%,#3a3a3a 45%,#0d0d0d 100%)}
.t-light{background:radial-gradient(circle at 50% 50%,#ffffff 0%,#cfd6dc 60%,#8fa0ab 100%)}
.t-black{background:radial-gradient(circle at 55% 45%,#777 0%,#141414 55%,#000 100%)}
.t-blue{background:linear-gradient(135deg,#b9e3ff,#2b8ee0 50%,#0a4f9a)}

/* testimonials */
.testimonials{top:1692px;height:528px;background:radial-gradient(ellipse at 60% 45%,#6a5a50 0%,#3b302b 50%,#1c1714 100%)}
.testimonials h2{position:absolute;top:62px;width:100%;color:var(--white)}
.testimonials .small{position:absolute;top:118px;left:190px;width:820px;color:#c9c9c9}
.quote{position:absolute;top:198px;width:247px;height:220px;background:var(--card);color:#ddd}
.quote p{font-size:10px;font-style:italic;line-height:17px;margin:30px 26px 0 40px;position:relative}
.quote p::before{content:"\201C";position:absolute;left:-20px;top:-8px;font-size:30px;font-style:normal;color:var(--white)}
.quote p::after{content:"\00BB";position:absolute;right:-6px;bottom:-8px;font-size:20px;font-style:normal;color:var(--white)}
.author{position:absolute;left:46px;top:156px;display:flex;align-items:center;gap:12px}
.avatar{width:34px;height:34px;border-radius:50%;background:linear-gradient(#b28a73,#5a3d30)}
.author b{display:block;font-weight:400;font-size:13px;color:var(--white)}
.author span{font-size:10px;color:#999}

/* diamond types */
.types{top:2220px;height:484px}
.types h2{position:absolute;top:80px;width:100%;color:#333}
.types .small{position:absolute;top:140px;left:210px;width:780px}
.types-visual{position:absolute;left:470px;top:220px;width:270px;height:240px;background:radial-gradient(ellipse at 50% 55%,#eef0f2 0%,#f7f8f9 45%,rgba(255,255,255,0) 72%)}
.type-list{position:absolute;top:224px;list-style:none}
.type-list li{display:flex;align-items:center;gap:10px;font-size:13px;color:#444;height:27.5px}

/* contact */
.contact{top:2704px;height:479px;background:var(--black);color:var(--white)}
.contact h2{position:absolute;top:46px;width:100%}
.contact .small{position:absolute;top:96px;left:180px;width:840px;color:#cfcfcf}
.field{position:absolute;left:158px;width:374px;height:33px;background:var(--field);color:#bbb;font-size:11px;padding:9px 16px}
.info{position:absolute;left:600px;top:164px;font-size:13px;line-height:25px;color:#eee}
.info b{font-weight:600;letter-spacing:.5px}
.social{display:flex;gap:6px;margin-top:8px}
.social span{width:22px;height:22px;border-radius:50%;background:var(--white)}

/* footer */
.footer{top:3183px;height:114px;background:var(--footer);text-align:center}
.footer ul{list-style:none;display:flex;justify-content:center;gap:26px;margin-top:38px}
.footer li{font-family:"Montserrat",Arial,sans-serif;font-size:12px;color:var(--white)}
.footer p{font-size:10px;color:#888;margin-top:10px}
</style>
</head>
<body>

<header class="hero">
  <div class="hero-photo" role="img" aria-label="Loose brilliant-cut diamonds on a blue surface"></div>
  <div class="topbar">
    <div class="brand">LUNACREST<br>GEMS</div>
    <ul class="nav">
      <li class="active">HOME</li><li>ABOUT US</li><li>CONTACT US</li><li>GALLERY</li><li>TESTIMONIALS</li><li>DIAMOND TYPES</li>
    </ul>
  </div>
  <div class="hero-band"></div>
  <div class="hero-title">Mauris vel lacus vitae felis vestibulum</div>
  <div class="hero-sub">Etiam est nunc venenatis in tristique</div>
  <div class="dots"><span></span><span></span><span></span></div>
</header>

<section class="about center">
  <h2>ABOUT US</h2>
  <p class="lead">Duis tincidunt lectus quis dui viverra vestibulum Suspendisse vulputate aliquam dui Nulla elementum dui ut augue Aliquam vehicula mi at mauris Maecenas placerat nisl at consequat</p>
  <p class="small">Mauris vel lacus vitae felis vestibulum volutpat Etiam est nunc venenatis in tristique eu imperdiet ac nisl Cum sociis natoque penatibus et magnis dis parturient montes nascetur ridiculus mus In iaculis facilisis massa Etiam eu urna Sed porta Suspendisse quam leo molestie sed luctus quis feugiat in pede Fusce tellus Sed metus augue convallis et vehicula ut pulvinar eu ante Integer orci tellus tristique vitae consequat nec porta vel lectus Nulla sit amet diam Duis non nunc</p>

  <div class="feature" style="left:200px">
    <svg width="64" height="54" viewBox="0 0 64 54"><path d="M14 2h36l12 16L32 52 2 18z" fill="#9a9a9a"/><path d="M2 18h60M14 2l8 16 10 34 10-34 8-16M22 18l10-16 10 16" stroke="#fff" stroke-width="2" fill="none"/></svg>
    <h3>Find Our Store</h3>
    <p>Spendisse quam leo molestie sed luctus quis feugiat in pede Fusce tellus Sed metus augue convallis et vehicula ut pulvinar ante</p>
  </div>
  <div class="feature" style="left:473px">
    <svg width="60" height="60" viewBox="0 0 60 60"><circle cx="30" cy="30" r="28" fill="#9a9a9a"/><circle cx="30" cy="30" r="18" fill="none" stroke="#fff" stroke-width="3"/><path d="M21 30l6 6 12-13" stroke="#fff" stroke-width="4" fill="none"/></svg>
    <h3>Why Choose Us</h3>
    <p>Spendisse quam leo molestie sed luctus quis feugiat in pede Fusce tellus Sed metus augue convallis et vehicula ut pulvinar ante</p>
  </div>
  <div class="feature" style="left:747px">
    <svg width="44" height="60" viewBox="0 0 44 60"><path d="M6 16a16 16 0 1 1 24 14c-5 3-6 6-6 12" stroke="#9a9a9a" stroke-width="9" fill="none"/><circle cx="24" cy="54" r="5" fill="#9a9a9a"/></svg>
    <h3>Ask for Help</h3>
    <p>Spendisse quam leo molestie sed luctus quis feugiat in pede Fusce tellus Sed metus augue convallis et vehicula ut pulvinar ante</p>
  </div>
</section>

<section class="gallery center" role="img" aria-label="Coastal New South Wales beach with turquoise sea and green headland">
  <h2>OUR GALLERY</h2>
  <p class="lead">Phasellus felis dolor scelerisque a tempus eget lobortis id libero Donec scelerisque leo ac risus</p>
  <div class="thumb t-silver" style="left:185px;top:156px" role="img" aria-label="Diamond on silver background"></div>
  <div class="thumb t-dark" style="left:400px;top:156px" role="img" aria-label="Scattered diamonds on dark cloth"></div>
  <div class="thumb t-light" style="left:615px;top:156px" role="img" aria-label="Diamonds on white"></div>
  <div class="thumb t-black" style="left:829px;top:156px" role="img" aria-label="Diamonds on black"></div>
  <div class="thumb t-blue" style="left:185px;top:310px" role="img" aria-label="Blue gemstones"></div>
  <div class="thumb t-dark" style="left:400px;top:310px" role="img" aria-label="Diamond close-up"></div>
  <div class="thumb t-black" style="left:615px;top:310px" role="img" aria-label="Pile of diamonds"></div>
  <div class="thumb t-dark" style="left:829px;top:310px" role="img" aria-label="Diamonds on dark surface"></div>
</section>

<section class="testimonials center" role="img" aria-label="Close-up of a jewelled ring and gemstones in warm low light">
  <h2>Testimonials</h2>
  <p class="small">Mauris vel lacus vitae felis vestibulum volutpat Etiam est nunc venenatis in tristique eu imperdiet ac nisl Cum sociis natoque penatibus et magnis dis parturient montes nascetur ridiculus mus In iaculis facilisis massa Etiam eu urna Sed porta Suspendisse quam leo molestie sed luctus quis feugiat in pede</p>
  <div class="quote" style="left:215px;text-align:center">
    <p>Mauris vel lacus vitae felis vestibulum volutpat Etiam est nunc venenatis in tristique eu imperdiet ac nisl Cum sociis natoque penatibus et magnis dis parturient montes nascetur ridiculus mus in iaculis facilisis</p>
    <div class="author" style="text-align:left"><div class="avatar" role="img" aria-label="Customer portrait"></div><div><b>By Author Name</b><span>Location Area</span></div></div>
  </div>
  <div class="quote" style="left:490px;text-align:center">
    <p>Mauris vel lacus vitae felis vestibulum volutpat Etiam est nunc venenatis in tristique eu imperdiet ac nisl Cum sociis natoque penatibus et magnis dis parturient montes nascetur ridiculus mus in iaculis facilisis</p>
    <div class="author" style="text-align:left"><div class="avatar" role="img" aria-label="Customer portrait"></div><div><b>By Author Name</b><span>Location Area</span></div></div>
  </div>
  <div class="quote" style="left:767px;text-align:center">
    <p>Mauris vel lacus vitae felis vestibulum volutpat Etiam est nunc venenatis in tristique eu imperdiet ac nisl Cum sociis natoque penatibus et magnis dis parturient montes nascetur ridiculus mus in iaculis facilisis</p>
    <div class="author" style="text-align:left"><div class="avatar" role="img" aria-label="Customer portrait"></div><div><b>By Author Name</b><span>Location Area</span></div></div>
  </div>
</section>

<section class="types center">
  <h2>Diamond Types</h2>
  <p class="small">Duis tincidunt lectus quis dui viverra vestibulum Suspendisse vulputate aliquam dui Nulla elementum dui ut augue Aliquam vehicula mi at mauris Maecenas placerat nisl at consequat rhoncus sem nunc gravida justo quis eleifend arcu velit quis lacus Morbi magna magna tincidunt</p>
  <div class="types-visual" role="img" aria-label="Faint large diamond in soft silver light"></div>
  <svg width="0" height="0" style="position:absolute"><defs><g id="gem"><path d="M3 0h10l3 4-8 9-8-9z" fill="#333"/><path d="M0 4h16M5 0l3 13 3-13" stroke="#fff" stroke-width="1" fill="none"/></g></defs></svg>
  <ul class="type-list" style="left:292px;text-align:left">
    <li><svg width="16" height="13"><use href="#gem"/></svg>Duis tincidunt lectus</li>
    <li><svg width="16" height="13"><use href="#gem"/></svg>Wuis dui viverra</li>
    <li><svg width="16" height="13"><use href="#gem"/></svg>Cestibulum</li>
    <li><svg width="16" height="13"><use href="#gem"/></svg>Suspendisse</li>
    <li><svg width="16" height="13"><use href="#gem"/></svg>vulputate aliquam</li>
  </ul>
  <ul class="type-list" style="left:508px;text-align:left">
    <li><svg width="16" height="13"><use href="#gem"/></svg>Suspendisse</li>
    <li><svg width="16" height="13"><use href="#gem"/></svg>Vulputate aliquam</li>
    <li><svg width="16" height="13"><use href="#gem"/></svg>Dui Nulla</li>
    <li><svg width="16" height="13"><use href="#gem"/></svg>Elementum</li>
    <li><svg width="16" height="13"><use href="#gem"/></svg>Aliquam</li>
  </ul>
  <ul class="type-list" style="left:721px;text-align:left">
    <li><svg width="16" height="13"><use href="#gem"/></svg>Duis tincidunt lectus</li>
    <li><svg width="16" height="13"><use href="#gem"/></svg>Wuis dui viverra</li>
    <li><svg width="16" height="13"><use href="#gem"/></svg>Cestibulum</li>
    <li><svg width="16" height="13"><use href="#gem"/></svg>Suspendisse</li>
    <li><svg width="16" height="13"><use href="#gem"/></svg>vulputate aliquam</li>
  </ul>
</section>

<section class="contact center">
  <h2>Contact Us</h2>
  <p class="small">Mauris vel lacus vitae felis vestibulum volutpat Etiam est nunc venenatis in tristique eu imperdiet ac nisl Cum sociis natoque penatibus et magnis dis parturient montes nascetur ridiculus mus In iaculis facilisis massa Etiam eu urna Sed porta Suspendisse quam leo molestie sed luctus quis feugiat in pede</p>
  <div class="field" style="top:169px;text-align:left">Your Name</div>
  <div class="field" style="top:215px;text-align:left">Email address</div>
  <div class="field" style="top:261px;text-align:left">Phone</div>
  <div class="field" style="top:307px;height:84px;text-align:left">Message</div>
  <div class="info" style="text-align:left">
    <b>LUNACREST GEMS</b><br>
    24 Harbour Lane #3B<br>
    Sydney 2000 NSW<br>
    +61 (2) 5550 1427<br>
    info@lunacrestgems.com.au
    <div class="social"><span></span><span></span><span></span><span></span></div>
  </div>
</section>

<footer class="footer">
  <ul><li>HOME</li><li>ABOUT US</li><li>CONTACT US</li><li>GALLERY</li><li>TESTIMONIALS</li><li>DIAMOND TYPES</li></ul>
  <p>© 2014 Company Name. All right reserved. Terms of Use</p>
</footer>

</body>
</html>
```